A start-up named "Corvane Therapeutics" - needs a new PowerPoint design

We need a new PowerPoint Design for an early-stage start-up named "Corvane Therapeutics" seeking to disrupt the current approach towards drug discovery within aging disorders.

We would like to build on Corvane's legacy, the founder of the modern science of genetics, by employing a multidisciplinary approach, experimenting, and providing elderly patients the attention they deserve.

We have selected the suffix "therapeutics" intentionally as it stands for (a medicine) the treatment of disease; the science of healing. Alzheimer’s treatment is a huge, urgent, unmet need:
- Shift from a disease-management system to a preventive medicine system
- Focus on increasing the health span, not only the life span

Target Market(s)

Pharma/ Biotech Executives Medical Institutions Healthcare professionals (MDs, nurses, payors, pharmacists, etc.) Patients

Industry/Entity Type

Healthcare

Other font styles liked:
• Celias

Colors
0054AA
0677BA
7BADD7
CADEEF
E8F1F8
E54698
E96AAD
F1A4CE
F9D9EA
FCEFF6
A7469A
B969AE
D3A5CF
EDDBEB
F8F0F9
6B429C
8869AF
B7A5CE
E3DAEB
F3F0F8

Requirements
Must have
• - differentiate from other companies named after Corvane - differentiate from other Pharma/ Biotech companies
Nice to have
• simplicity/ minimalist logo vivid colors gradient 3D Life-Sciences inspired Simple geometry Balance
Should not have
• mascot/ emblem watermark logo animated ink style nature-inspired inventive typography artistic chaos

```html
<!DOCTYPE html>
<html lang="en">
<head>
<meta charset="utf-8">
<title>Corvane Therapeutics – Presentation Template, Part 1</title>
<link href="https://fonts.googleapis.com/css2?family=Arimo:wght@400;700&display=swap" rel="stylesheet">
<style>
  :root{
    --blue-deep:#0054AA;
    --blue:#0677BA;
    --blue-soft:#7BADD7;
    --blue-pale:#CADEEF;
    --pink:#E54698;
    --pink-soft:#E96AAD;
    --magenta:#A7469A;
    --purple:#6B429C;
    --purple-band:#632D8F;
    --ink:#1a1a1a;
    --grey:#777;
    --white:#fff;
  }
  *{margin:0;padding:0;box-sizing:border-box}
  html,body{width:1200px;height:1200px;overflow:hidden;background:var(--white)}
  body{position:relative;font-family:"Arimo",Arial,sans-serif;color:var(--ink)}
  .slide{position:absolute;width:516px;height:291px;overflow:hidden;background:var(--white)}
  .s1{left:61px;top:55px}
  .s2{left:617px;top:55px}
  .s3{left:61px;top:381px}
  .s4{left:617px;top:381px}
  .s5{left:61px;top:699px;width:515px;height:289px}
  .abs{position:absolute}

  .photo-lab{position:absolute;inset:0;
    background:linear-gradient(120deg,#9fd6f2 0%,#6fa7e8 30%,#c58ed6 55%,#7fc4ea 80%,#4fb6d8 100%);
    clip-path:polygon(302px 0,516px 0,516px 291px,175px 291px)}
  .s1 .bg{position:absolute;inset:0;background:linear-gradient(100deg,var(--pink) 0%,#d452a6 40%,var(--purple) 75%)}

  .brand{position:absolute;left:22px;top:30px;display:flex;align-items:center;gap:7px;color:var(--white)}
  .brand-mark{width:30px;height:30px;border:2.5px solid currentColor}
  .brand-name{font-weight:400;font-size:19px;line-height:17px}
  .brand-name small{display:block;font-size:8.5px;line-height:10px;letter-spacing:1.2px}
  .s2 .brand{color:var(--blue-deep)}

  .title{position:absolute;left:22px;top:97px;font-weight:700;font-size:29px;line-height:31px;color:var(--white)}
  .rule{position:absolute;left:21px;width:34px;height:3px;background:var(--white)}
  .subtitle{position:absolute;left:21px;top:180px;font-weight:700;font-size:13.5px;color:var(--white)}
  .date{position:absolute;left:21px;top:200px;font-size:9.5px;color:var(--white)}
  .s2 .title{color:var(--blue-deep)}
  .s2 .rule{background:var(--pink)}
  .s2 .subtitle{color:var(--pink)}
  .s2 .date{color:var(--grey)}

  .heading{position:absolute;left:16px;top:21px;font-weight:700;font-size:16px;color:var(--blue-deep)}
  .corner-mark{position:absolute;right:16px;top:18px;width:22px;height:22px;border:2px solid var(--purple)}
  .bullets{position:absolute;left:16px;top:62px;width:485px;list-style:none}
  .bullets li{position:relative;padding-left:8px;font-size:10.5px;line-height:13px}
  .bullets li::before{content:"•";position:absolute;left:0;color:var(--pink)}
  .bullets li.sub{margin-top:5px;padding-left:15px;font-size:9.3px;line-height:11.5px}
  .bullets li.sub::before{content:"-";left:8px}

  .footer{position:absolute;left:0;bottom:0;width:100%;height:21px;
    background:linear-gradient(90deg,var(--pink-soft) 0%,var(--pink) 35%,var(--magenta) 65%,var(--purple) 100%);
    color:var(--white);font-size:5px;display:flex;align-items:center;justify-content:space-between;padding:0 16px}
  .footer b{font-size:5.5px}

  .mission-copy{position:absolute;left:16px;width:240px;font-size:7.8px;line-height:10.3px}
  .section-head{position:absolute;left:16px;top:157px;font-weight:700;font-size:10px;color:var(--pink)}
  .photo-scientist{position:absolute;left:279px;top:0;width:237px;height:270px;
    background:linear-gradient(160deg,#8fc3ee 0%,#3f86d0 45%,#1d5aa8 100%)}
  .photo-scientist .corner-mark{right:16px;top:18px;border-color:var(--white)}

  .s5 .bg{position:absolute;inset:0;background:linear-gradient(110deg,#e05aa8 0%,#c063b6 45%,#7c4aa6 100%)}
  .break-title{position:absolute;left:22px;top:104px;font-weight:700;font-size:44px;line-height:48px;color:var(--white)}
  .break-copy{position:absolute;left:21px;top:185px;width:470px;font-size:8px;line-height:10px;color:var(--white)}

  .part-band{position:absolute;left:0;top:1050px;width:1200px;height:126px;background:var(--purple-band)}
  .part-label{position:absolute;left:62px;top:16px;font-weight:700;font-size:80px;line-height:90px;color:var(--white);letter-spacing:1px}
</style>
</head>
<body>

<section class="slide s1">
  <div class="bg"></div>
  <div class="photo-lab" role="img" aria-label="Photo of a scientist in safety glasses pipetting into petri dishes beside test tubes"></div>
  <div class="brand"><span class="brand-mark"></span><span class="brand-name">Corvane<small>Therapeutics</small></span></div>
  <h1 class="title">Presentation<br>Title</h1>
  <div class="rule" style="top:168px"></div>
  <div class="subtitle">Subtitle</div>
  <div class="date">Date: XX/XX/XX</div>
</section>

<section class="slide s2">
  <div class="photo-lab" role="img" aria-label="Photo of a scientist in safety glasses pipetting into petri dishes beside test tubes"></div>
  <div class="brand"><span class="brand-mark"></span><span class="brand-name">Corvane<small>Therapeutics</small></span></div>
  <h1 class="title">Presentation<br>Title</h1>
  <div class="rule" style="top:168px"></div>
  <div class="subtitle">Subtitle</div>
  <div class="date">Date: XX/XX/XX</div>
</section>

<section class="slide s3">
  <h2 class="heading">Template Style Option</h2>
  <span class="corner-mark"></span>
  <ul class="bullets">
    <li>Lorem ipsum dolor sit amet, consectetur adipiscing elit. Curabitur at fringilla velit. In ac sagittis nulla. Nulla quis erat et ligula aliquam sagittis in viverra mauris. Pellentesque pharetra hendrerit orci at.</li>
    <li class="sub">Donec vel suscipit purus, ultrices ornare neque. Sed nec est a lacus lacinia venenatis non at est. Vestibulum vitae lorem lectus. Phasellus gravida mauris a sapien elementum malesuada. Vestibulum ut urna eu dolor suscipit condimentum. Curabitur sed commodo leo. Phasellus faucibus sem ante.</li>
  </ul>
  <div class="footer"><span>Copywrite Statement 2022</span><b>3</b></div>
</section>

<section class="slide s4">
  <h2 class="heading">Our Mission</h2>
  <p class="mission-copy" style="top:59px">Lorem ipsum dolor sit amet, consectetur adipiscing elit. Curabitur at fringilla velit. In ac sagittis nulla. Nulla quis erat et ligula aliquam sagittis in viverra mauris. Pellentesque pharetra hendrerit orci at. Donec vel suscipit purus, ultrices ornare neque. Sed nec est a lacus lacinia venenatis non at est. Vestibulum vitae lorem lectus. Phasellus gravida mauris a sapien elementum malesuada. Vestibulum ut urna eu dolor.</p>
  <h3 class="section-head">Section Header</h3>
  <p class="mission-copy" style="top:172px">Donec vel suscipit purus, ultrices ornare neque. Sed nec est a lacus lacinia venenatis non at est. Vestibulum vitae lorem lectus. Phasellus gravida mauris a sapien elementum malesuada. Vestibulum ut urna eu dolor.</p>
  <div class="photo-scientist" role="img" aria-label="Photo of a scientist in a lab coat holding a test tube over her notes in a blue-lit laboratory"><span class="corner-mark"></span></div>
  <div class="footer"><span>Copywrite Statement 2022</span><b>4</b></div>
</section>

<section class="slide s5">
  <div class="bg" role="img" aria-label="Pink and purple tinted photo of a gloved hand pipetting into a rack of vials"></div>
  <div class="brand"><span class="brand-mark"></span><span class="brand-name">Corvane<small>Therapeutics</small></span></div>
  <h1 class="break-title">Break Slide</h1>
  <div class="rule" style="top:167px"></div>
  <p class="break-copy">Donec vel suscipit purus, ultrices ornare neque. Sed nec est a lacus lacinia venenatis non at est. Vestibulum vitae lorem lectus. Phasellus gravida mauris a sapien elementum malesuada. Vestibulum ut urna eu dolor.</p>
</section>

<div class="part-band"><div class="part-label">PART 1</div></div>

</body>
</html>
```